High-end executive coaching group needs a 2 page digital flyer

We need a 2 page digital flyer for a high end leadership coaching offering for global leaders in healthcare. The flyer will advertise a new service (an elite senior leadership coaching group) for senior leaders in the healthcare industry from around the world.
The flyer should be upmarket, professional and minimalist in style to meet the expectations of my professional market (very senior doctors and executives).
The design should be based on my existing logo and brand, see my landing page: www.marlowadvisory.com
The key elements needed are
1) An editable PDF which we can update as we revise the specific details of the offering. The text and draft design for this is attached.
2) The banner image should be high quality but abstract. It can be based on the landing page of my website (the two ripple effects) but does not need to strictly adhere to this.
3) The logo placement of the Marlow Advisory delta sign should be discreet so that it does not dominate
4) The small logos of our professional accrediting organisations should be discreetly placed at the end and should not dominate. They might work best as mono icons in a footer (e.g. blue on a white background, or white on blue.
5) Please find enclosed a previous flyer as an example of a similar style we have used for more junior professionals. The design worked quite well, although we now need a more upmarket version for our senior executives.

Please note this design specifically needs to use existing branding and images from my website: marlowadvisory.com. We are definitely not looking for stock "leadership team" images for this high-end brochure.

Target Market(s)

Senior global leaders in the healthcare industry

Industry/Entity Type

Leading business schools & Healthcare industry.

Font styles to use
Other font styles liked:
• Operetta (selective use for heading) and Sofia Pro (body text)

Colors
0054AA
0677BA
7BADD7
CADEEF
E8F1F8

Requirements
Must have
• Clean minimalist and high professionally look that directly speaks to the interests and perspectives of senior leader leaders in healthcare. It also needs very clear call to action sections
Nice to have
• Effective presentation of the two bios and photographs. These need to look impressive, but should not dominate.
Should not have
• Loud and bold colours, large use of logos.

```html
<!DOCTYPE html>
<html lang="en">
<head>
<meta charset="utf-8">
<title>Marlow Advisory – Analytic Coaching Group Flyer</title>
<link rel="stylesheet" href="https://fonts.googleapis.com/css2?family=Figtree:ital,wght@0,400;0,500;0,600;0,700;1,400;1,500&family=Playfair+Display:wght@500;600;700&display=swap">
<style>
:root{
  --blue-deep:#0054AA;
  --blue-mid:#0677BA;
  --blue-soft:#7BADD7;
  --blue-pale:#CADEEF;
  --blue-mist:#E8F1F8;
  --ink:#2b2b2b;
  --backdrop:#B4B0B0;
  --serif:"Playfair Display", Georgia, serif;
  --sans:"Figtree", Arial, sans-serif;
}
*{margin:0;padding:0;box-sizing:border-box}
html,body{width:1200px;height:900px;overflow:hidden}
body{background:var(--backdrop);position:relative;font-family:var(--sans);color:var(--ink)}
.page{position:absolute;top:78px;width:524px;height:744px;background:#fff;overflow:hidden}
.page--front{left:54px}
.page--back{left:622px}
.abs{position:absolute}

/* front page */
.hero-visual{left:0;top:0;width:524px;height:161px;
  background:radial-gradient(ellipse at 68% 60%,#c9d3dd 0%,#dfe6ee 35%,#eef2f7 70%,#f6f8fb 100%)}
.brand-name{left:431px;top:26px;font-family:var(--serif);font-weight:500;font-size:17px;line-height:16px;color:var(--blue-deep)}
.brand-mark{left:412px;top:33px;width:12px;height:12px;border-radius:50%;background:var(--blue-deep)}
.hero-title{left:46px;top:55px;font-family:var(--serif);font-weight:700;font-size:34px;line-height:42px;color:var(--blue-deep);letter-spacing:.1px}
.hero-band{left:0;top:161px;width:524px;height:61px;background:var(--blue-deep)}
.hero-band p{position:absolute;left:46px;top:11px;width:470px;color:#fff;font-weight:600;font-size:13.2px;line-height:18.2px}
.deco{left:0;top:0}
.section-title{font-family:var(--serif);font-weight:500;font-size:18.5px;color:var(--blue-deep)}
.intro-lead{left:46px;top:286px;width:440px;font-weight:600;font-size:10.8px;line-height:13.6px}
.intro-body{left:46px;top:328px;width:440px;font-size:10.8px;line-height:13.6px}
.benefits{left:44px;top:418px;width:228px;list-style:none}
.benefits li,.questions li{position:relative;padding-left:16px;font-size:10.2px;line-height:12.5px;margin-bottom:4.2px}
.benefits li::before,.questions li::before{content:"";position:absolute;left:2px;top:1px;width:4px;height:7px;border:solid var(--blue-deep);border-width:0 2px 2px 0;transform:rotate(40deg)}
.benefits strong{color:var(--blue-mid);font-weight:500}
.quote-mark{font-family:var(--serif);font-weight:700;color:var(--blue-soft);font-size:34px;line-height:1}
.quote-front{left:312px;top:398px;width:158px;font-style:italic;font-size:14px;line-height:16.5px;color:var(--blue-deep)}
.quote-by{font-size:9px;font-weight:500}
.cta-left{left:33px;top:636px;width:150px;font-size:13.4px;line-height:18.5px;color:var(--blue-mid);font-weight:500}
.details{left:222px;top:630px;border-collapse:collapse;font-size:9.6px}
.details th{text-align:left;color:var(--blue-deep);font-weight:700;width:83px;padding:1.5px 0;vertical-align:top}
.details td{padding:1.5px 0;font-weight:500}
.details .note{color:var(--blue-mid);font-style:italic;font-weight:400;font-size:8.6px}
.rule-bottom{left:0;bottom:0;width:524px;height:4px;background:var(--blue-deep)}

/* back page */
.sky-visual{left:0;top:0}
.lead-title{left:46px;top:41px;width:260px;font-family:var(--serif);font-weight:600;font-size:16.5px;line-height:22.5px;color:var(--blue-mid)}
.ribbon{left:0;top:0}
.ribbon-name{font-family:var(--serif);font-weight:600;font-size:12.4px;color:#fff}
.portrait{background:linear-gradient(160deg,#6f8b55 0%,#8fa57a 40%,#3e5a86 100%)}
.portrait--two{background:linear-gradient(170deg,#151515 0%,#3a2520 45%,#d9a9a0 100%)}
.bio{font-size:10px;line-height:12px}
.engage{left:46px;top:464px;width:240px;font-size:12.8px;line-height:15px;color:var(--blue-mid);font-weight:500}
.questions{left:44px;top:524px;width:215px;list-style:none}
.questions li{font-weight:600;font-size:10px;margin-bottom:6.5px}
.quote-back{left:325px;top:470px;width:160px;font-style:italic;font-size:11.3px;line-height:13.5px;color:var(--blue-deep)}
.cta-band{left:0;top:635px;width:524px;height:73px;background:var(--blue-mist)}
.cta-label{font-size:9.6px;font-weight:700;color:var(--blue-deep);letter-spacing:.2px}
.cta-text{font-size:10px;line-height:12.6px;margin-top:6px}
.cta-contact{font-size:10px;line-height:12.6px;margin-top:6px;font-weight:600}
.footer{left:0;top:708px;width:524px;height:36px;background:var(--blue-deep)}
.footer-url{position:absolute;left:46px;top:11px;color:#fff;font-weight:700;font-size:10.6px}
.badges{position:absolute;left:297px;top:11px;display:flex;gap:20px;align-items:center}
.badge{background:#fff;opacity:.85}
</style>
</head>
<body>

<section class="page page--front">
  <div class="abs hero-visual" role="img" aria-label="Abstract water ripples in soft silver-blue tones"></div>
  <div class="abs brand-mark"></div>
  <div class="abs brand-name">Marlow<br>Advisory</div>
  <h1 class="abs hero-title">Elevate and Ignite<br>Your Leadership</h1>

  <svg class="abs deco" width="524" height="744" viewBox="0 0 524 744">
    <polygon points="363,222 524,222 524,319" fill="#E8F1F8"/>
    <polygon points="0,450 25,462 25,606 0,606" fill="#CADEEF"/>
    <polygon points="0,606 285,606 307,620 201,620 201,725 524,725 524,744 0,744" fill="#CADEEF"/>
    <polygon points="201,620 307,620 285,606 201,606" fill="#CADEEF"/>
    <polygon points="435,725 524,725 524,744" fill="#E8F1F8"/>
  </svg>

  <div class="abs hero-band">
    <p>Transformative conversations for senior healthcare leaders. Unlock purpose, engage authentically and amplify your leadership impact.</p>
  </div>

  <h2 class="abs section-title" style="left:46px;top:245px">Analytic Coaching Group for Senior Leaders</h2>
  <p class="abs intro-lead">As a senior leader in healthcare, you’re constantly navigating challenges.<br>But where do you turn for authentic connections, reflection and personal growth?</p>
  <p class="abs intro-body">Rethink your leadership assumptions and approach challenges with fresh creativity. Secure your spot in our exclusive Analytic Coaching Group and ignite your leadership potential.</p>

  <h2 class="abs section-title" style="left:46px;top:380px">Benefits to you</h2>
  <ul class="abs benefits">
    <li><strong>Transformative conversations:</strong> Engage in discussions that spark innovative leadership</li>
    <li><strong>Peer insights:</strong> Harness fresh insights from peers, enhancing your decision-making and effectiveness</li>
    <li><strong>Reimagined leadership:</strong> Channel your creativity and redefine your leadership, personally and professionally</li>
    <li><strong>Instant 360° insights:</strong> Gain real-time feedback from trusted peers to enrich your leadership</li>
    <li><strong>Lead authentically:</strong> Develop effective strategies using the latest insights from group and leadership psychology</li>
  </ul>

  <div class="abs quote-mark" style="left:287px;top:396px">“</div>
  <blockquote class="abs quote-front">You bare your heart and share things you wouldn’t under normal circumstances. You get to know each other very quickly. There’s that sort of intense, shared experience that comes from speaking to each other’s lives.
    <p class="quote-by" style="font-style:normal;color:var(--ink);margin-top:12px">Sarah, Medical Director</p>
  </blockquote>
  <div class="abs quote-mark" style="left:462px;top:548px">”</div>

  <p class="abs cta-left">Secure your spot now and&nbsp; ignite your leadership potential..</p>
  <table class="abs details">
    <tr><th>DATES:</th><td>7 February 2024 – 11 December 2024</td></tr>
    <tr><th>TIME:</th><td>7:30am - 8:45am (UK time).</td></tr>
    <tr><th>COMMITMENT:</th><td>Wednesdays, every 2 weeks</td></tr>
    <tr><th>LOCATION:</th><td>Connect from anywhere by video call</td></tr>
    <tr><th>COST:</th><td>£3350 (UK) | €3900 (EU) | A$6530 (AU)</td></tr>
    <tr><th></th><td class="note">Payment options available</td></tr>
  </table>
  <div class="abs rule-bottom"></div>
</section>

<section class="page page--back">
  <svg class="abs sky-visual" width="524" height="200" viewBox="0 0 524 200" role="img" aria-label="Pale grey cloudy sky with a single bird in flight">
    <defs><linearGradient id="sky" x1="0" y1="0" x2="1" y2="1"><stop offset="0" stop-color="#eeeeef"/><stop offset="1" stop-color="#d9dadc"/></linearGradient></defs>
    <polygon points="200,0 524,0 524,191" fill="url(#sky)"/>
  </svg>

  <h2 class="abs lead-title">Expertly guided by insight,<br>academic rigour and practical<br>leadership strategies</h2>

  <svg class="abs ribbon" width="524" height="330" viewBox="0 0 524 330">
    <polygon points="58,126 343,126 384,151 58,151" fill="#0054AA"/>
    <polygon points="145,298 462,298 462,323 186,323" fill="#0054AA"/>
  </svg>
  <div class="abs ribbon-name" style="left:181px;top:130px">Professor Daniel Marlow</div>
  <div class="abs ribbon-name" style="left:197px;top:302px">Dr Helen Ashcroft</div>

  <div class="abs portrait" style="left:46px;top:136px;width:124px;height:146px" role="img" aria-label="Portrait photograph of Professor Daniel Marlow"></div>
  <p class="abs bio" style="left:181px;top:164px;width:292px">Professor Daniel Marlow has 30 years’ experience developing leaders. An award-winning business school professor, group analyst and psychoanalytic psychotherapist, he has taught senior leadership programmes at the University of Wessex, Thames College London and the University of Southbank. His extensive leadership experience as a public health service clinical director and consultant psychotherapist inform his work as an IACC accredited executive coach. With a PhD from Kingsway Institute, Harbourside, he is an expert in melding psychological insights with strategic organisational change.</p>

  <div class="abs portrait portrait--two" style="left:354px;top:308px;width:126px;height:133px" role="img" aria-label="Portrait photograph of Dr Helen Ashcroft"></div>
  <p class="abs bio" style="left:46px;top:336px;width:298px">Dr Helen Ashcroft is a renowned psychoanalyst, group analyst, consultant psychiatrist and organisational consultant in the health sector. She has 20 years of leadership within the public health service, and she was also the National Director of Therapies for the Cedarwood Group, directing therapy services across 100 hospitals. She holds prominent positions as Chair of the Patient Safety Group, Chair of the Working Group on Clinician Wellbeing after Serious Incidents, and Vice Chair of the Psychotherapy Faculty at the Royal Society of Psychiatric Medicine.</p>

  <p class="abs engage">Engage with global leaders, gain diverse insights and forge lasting bonds. Explore questions such as:</p>
  <ul class="abs questions">
    <li>What kind of leader do I aspire to be in the next chapter of my life and career?</li>
    <li>What unique qualities and actions do I offer that no one else can?</li>
    <li>How can I galvanise my personal strengths to inspire and motivate others?</li>
  </ul>

  <div class="abs quote-mark" style="left:306px;top:470px;font-size:26px">“</div>
  <blockquote class="abs quote-back">Through this exceptional coaching, our leadership team elevated its performance to lead the hospital with greater clarity, cohesion and thoughtfulness. Not only do we provide a superior work environment for staff, but better care for our patients.
    <p class="quote-by" style="font-style:normal;color:var(--ink);margin-top:9px">John, CEO</p>
  </blockquote>
  <div class="abs quote-mark" style="left:469px;top:583px;font-size:26px">”</div>

  <div class="abs cta-band">
    <div class="abs" style="left:46px;top:14px;width:240px">
      <p class="cta-label">LIMITED SPOTS AVAILABLE</p>
      <p class="cta-text">Don’t miss this unique opportunity to<br>transform your leadership journey.</p>
    </div>
    <div class="abs" style="left:309px;top:14px;width:210px">
      <p class="cta-label">BOOK YOUR FREE DISCOVERY CALL</p>
      <p class="cta-contact">daniel@marlowadvisory.com<br>helenashcroft@mailbox.com</p>
    </div>
  </div>

  <footer class="abs footer">
    <span class="footer-url">www.marlowadvisory.com</span>
    <div class="badges">
      <span class="badge" style="width:14px;height:14px;border-radius:50%"></span>
      <span class="badge" style="width:30px;height:9px"></span>
      <span class="badge" style="width:26px;height:13px"></span>
      <span class="badge" style="width:38px;height:10px"></span>
    </div>
  </footer>
</section>

</body>
</html>
```